Business Card Design

Tumble Harbor is a Laundromat Store
we provide wash and Fold service to Customers who are busy with their life and can not come to the store and do laundry
we have customers who drop their laundry at the store
but now i want to provide service to customers who are not able to come to the store to drop. i will go to their address and pickup the laundry and get it washed folded and delivered
Updates
Can you use the colour in you design which i uploaded and also fusha fluorescent green bright pink
Target Market(s)
all works of life who don't have time to do laundry
Industry/Entity Type
Store
Contact Information for Business Card
TumbleHarbor Laundromat
247 Mallory Street
Lynn MA 01938
Look and feel
Each slider illustrates characteristics of the customer's brand and the style your logo design should communicate.

```html
<!DOCTYPE html>
<html lang="en">
<head>
<meta charset="utf-8">
<title>Tumble Harbor Laundromat – Business Card</title>
<link href="https://fonts.googleapis.com/css2?family=Lato:wght@400;700;900&family=Montserrat:wght@500;700&display=swap" rel="stylesheet">
<style>
  :root {
    --backdrop: #3a3a3a;
    --pink: #e8168c;
    --pink-light: #f250a9;
    --green: #1e9a52;
    --green-dark: #0f7a3c;
    --green-light: #35b86a;
    --purple: #8a2c8e;
    --purple-dark: #6e1f72;
    --white: #ffffff;
    --yellow: #ffe94a;
    --cloth-mix: #b45b7d;
    --cloth-stack: #8c5d54;
  }
  * { box-sizing: border-box; margin: 0; padding: 0; }
  html, body { width: 1200px; height: 900px; overflow: hidden; }
  body {
    background: var(--backdrop);
    font-family: "Lato", sans-serif;
    position: relative;
  }
  .business-card {
    position: absolute;
    left: 60px; top: 140px;
    width: 1080px; height: 620px;
    overflow: hidden;
    background: radial-gradient(ellipse at 50% 45%, var(--pink-light) 0%, var(--pink) 60%);
    box-shadow: 0 20px 50px rgba(0,0,0,.45);
  }
  .card-shapes { position: absolute; inset: 0; }
  .brand-name {
    position: absolute; top: 28px; left: 0; right: 0;
    text-align: center;
    font-family: "Montserrat", sans-serif;
    font-weight: 700; font-size: 46px;
    color: var(--white);
    display: flex; justify-content: center; align-items: center; gap: 14px;
  }
  .brand-mark { width: 22px; height: 22px; background: var(--green); }
  .address {
    position: absolute; top: 102px; left: 0; right: 0;
    text-align: center;
    font-family: "Montserrat", sans-serif; font-weight: 700;
    font-size: 25px; letter-spacing: 4px;
    color: var(--white);
  }
  .call-box {
    position: absolute; top: 146px; left: 50%;
    transform: translateX(-50%);
    background: var(--purple);
    padding: 5px 16px;
    font-family: "Montserrat", sans-serif; font-weight: 700;
    font-size: 27px; color: var(--white); white-space: nowrap;
  }
  .call-box .phone { color: var(--yellow); }
  .from-to-label {
    position: absolute;
    font-family: "Montserrat", sans-serif; font-weight: 700;
    color: var(--white); font-size: 34px;
  }
  .from-label { left: 500px; top: 236px; }
  .to-label { left: 515px; top: 290px; }
  .step-caption {
    position: absolute; top: 510px; width: 220px;
    text-align: center;
    font-weight: 900; font-size: 23px; line-height: 1.2;
    color: var(--white);
  }
</style>
</head>
<body>
  <div class="business-card">
    <svg class="card-shapes" width="1080" height="620" viewBox="0 0 1080 620">
      <defs>
        <linearGradient id="greenBand" x1="0" y1="0" x2="0" y2="1">
          <stop offset="0" stop-color="var(--green-light)"/>
          <stop offset="1" stop-color="var(--green-dark)"/>
        </linearGradient>
      </defs>
      <path d="M0 340 Q540 215 1080 340 L1080 620 L0 620 Z" fill="url(#greenBand)"/>
      <path d="M0 340 Q540 215 1080 340" fill="none" stroke="var(--purple-dark)" stroke-width="8"/>

      <rect role="img" aria-label="Pile of mixed dirty laundry" x="300" y="200" width="200" height="160" rx="40" fill="var(--cloth-mix)"/>
      <rect role="img" aria-label="Stack of neatly folded clean clothes" x="620" y="180" width="200" height="180" rx="10" fill="var(--cloth-stack)"/>

      <circle cx="560" cy="280" r="82" fill="var(--purple)" stroke="var(--white)" stroke-width="3"/>
      <path d="M488 283 H630 M618 273 L632 283 L618 293" fill="none" stroke="var(--white)" stroke-width="4"/>

      <g stroke="var(--white)" stroke-width="4" fill="var(--white)">
        <circle cx="170" cy="440" r="58"/>
        <circle cx="420" cy="440" r="58"/>
        <circle cx="670" cy="440" r="58"/>
        <circle cx="920" cy="440" r="58"/>
      </g>
      <rect role="img" aria-label="Schedule calendar icon" x="130" y="405" width="80" height="70" rx="6" fill="#6d6d6d"/>
      <rect role="img" aria-label="House pick-up icon" x="382" y="402" width="76" height="76" rx="6" fill="#4a8fd6"/>
      <rect role="img" aria-label="Washing machines icon" x="630" y="408" width="80" height="64" rx="6" fill="#8a8a8a"/>
      <circle role="img" aria-label="Happy customer emoji icon" cx="920" cy="440" r="38" fill="#f5c518"/>

      <g fill="none" stroke="var(--white)" stroke-width="3">
        <path d="M245 440 Q290 420 335 440 M325 430 L337 441 L323 448"/>
        <path d="M495 440 Q540 420 585 440 M575 430 L587 441 L573 448"/>
        <path d="M745 440 Q790 420 835 440 M825 430 L837 441 L823 448"/>
      </g>
    </svg>

    <div class="brand-name"><span class="brand-mark"></span>TumbleHarbor Laundromat</div>
    <div class="address">247 MALLORY STREET LYNN MA 01938</div>
    <div class="call-box">CALL US: <span class="phone">079 555 01234</span></div>

    <div class="from-to-label from-label">FROM</div>
    <div class="from-to-label to-label">TO</div>

    <div class="step-caption" style="left:60px">You Schedule<br>A Pick-Up</div>
    <div class="step-caption" style="left:310px">We Pick-Up<br>Your Dirty Laundry</div>
    <div class="step-caption" style="left:560px">We Wash, Dry, Fold<br>&amp; Return Clean Laundry</div>
    <div class="step-caption" style="left:810px">Enjoy Effortless<br>Clean Laundry</div>
  </div>
</body>
</html>
```